New Dynamic Design Based on Other Site

We need a new website designed where the front page is VERY SEO Friendly. The front page should almost follow the same SEO principles that are on RankLoomPress.com. The inner pages need to follow the same exact video animations that occur on vollq.com. I'd like to keep our "marbletons" theme throughout the new design but we will provide all of the content but I want someone to design something SEO friendly, new blog theme, and actual inner pages that are dynamic and based on those short videos.

Check attached file for company name and site that we currently have. Feel free to pull the content from that site and re-use it and also leave placeholders for the rest of them.

PLEASE NO USE OF STOCK IMAGES. Use a designer or an illustrator to create the various images.

Please make sure the front page is SEO friendly! Make sure you familiarize yourself with the quorvix algorithm for SEO. Content above the fold H1 Tags Very mobile friendly Minimal javascript and animations Basically a quality static page with optimized content

Target Market(s)

call center companies, anything call related

Industry/Entity Type

Telecommunications

Number of Pages Required

4 page

Font styles to use
Sans Serif

Colors
33a6d7
85cae6
0792cd
0255a3
cee9f5
ecf7fb
ffffff

Requirements
Must have
• places for video animations
• dynamic functionality
• SEO friendly (front page)
Should not have
• should not look like a template. needs to be unique

```html
<!DOCTYPE html>
<html lang="en">
<head>
<meta charset="utf-8">
<title>DialMetric – Contact</title>
<link rel="stylesheet" href="https://fonts.googleapis.com/css2?family=Open+Sans:wght@400;600;700&display=swap">
<style>
:root{
  --blue:#33a6d7;
  --blue-light:#85cae6;
  --blue-mid:#0792cd;
  --navy:#0255a3;
  --ink:#1f3350;
  --hero:#72b8a3;
  --hero-deep:#88c9b3;
  --map:#d6d6d6;
  --line:#d9dde2;
  --white:#ffffff;
  --text:#222;
}
*{box-sizing:border-box;margin:0;padding:0}
html,body{width:741px;height:1200px;overflow:hidden;background:var(--white)}
body{position:relative;font-family:"Open Sans",Arial,sans-serif;color:var(--text)}
.abs{position:absolute}

/* header */
.site-header{position:absolute;left:0;top:0;width:741px;height:82px;background:var(--white)}
.brand{left:78px;top:30px;display:flex;align-items:center;gap:6px;font-size:19px;font-weight:600;color:var(--navy)}
.brand-dot{width:16px;height:16px;border-radius:50%;background:var(--blue)}
.call{left:444px;top:18px;display:flex;align-items:center;gap:7px}
.call-icon{width:19px;height:19px;border-radius:50%;background:var(--blue);display:flex;align-items:center;justify-content:center}
.call-label{font-size:7px;color:var(--ink);line-height:1.1}
.call-number{font-size:11px;font-weight:700;color:var(--blue)}
.search{left:562px;top:15px;width:94px;height:23px;border:1px solid var(--line);font-size:5.5px;color:#555;display:flex;align-items:center;gap:5px;padding-left:10px}
.nav{top:56px;font-size:6.5px;font-weight:600;color:var(--ink);letter-spacing:.2px}
.nav.is-active{color:var(--blue)}
.login{left:608px;top:52px;width:48px;height:18px;background:var(--blue);color:var(--white);font-size:6.5px;display:flex;align-items:center;justify-content:center;gap:4px}

/* hero */
.hero{left:0;top:82px;width:741px;height:255px;background:var(--hero)}
.hero-kicker{left:99px;top:174px;font-size:13px;font-weight:600;color:var(--white)}
.hero-title{left:99px;top:189px;font-size:21px;font-weight:700;color:var(--white);letter-spacing:.2px}
.hero-sub{left:277px;top:219px;font-size:10px;font-weight:600;color:var(--white)}
.hero-art{left:312px;top:96px;width:410px;height:241px;background:radial-gradient(circle at 70% 45%,var(--hero-deep),var(--hero) 70%)}

/* contact */
.section-title{left:0;top:370px;width:741px;text-align:center;font-size:11.5px;font-weight:700;color:var(--ink)}
.title-rule{left:356px;top:395px;width:28px;height:1px;background:var(--blue)}
.map{left:86px;top:438px;width:374px;height:244px;background:linear-gradient(160deg,#dadada,#cfcfcf)}
.addr-head{left:495px;top:486px;font-size:11px;font-weight:700;color:var(--ink)}
.addr-line{left:495px;font-size:11px;color:var(--text);font-variant:small-caps}
.addr-rule{left:495px;width:149px;height:1px;background:var(--line)}
.addr-mail{left:495px;top:576px;font-size:9.5px}
.addr-phone{left:495px;top:607px;font-size:11px}

/* form */
.form{left:87px;top:720px;width:565px;height:207px;border:1px solid var(--line)}
.field{position:absolute;border:1px solid var(--line);font-size:6px;color:#666;padding:9px 10px}
.submit{position:absolute;left:27px;top:158px;width:72px;height:24px;background:var(--blue);color:var(--white);font-size:7.5px;font-weight:700;display:flex;align-items:center;justify-content:center}

/* footer */
.footer{left:0;top:970px;width:741px;height:230px;background:var(--navy);color:var(--white)}
.f-head{top:40px;font-size:7px;font-weight:700}
.f-list{top:58px;font-size:6px;line-height:10px;font-variant:small-caps}
.f-input{left:341px;top:59px;width:145px;height:24px;background:var(--white);color:var(--navy);font-size:6px;display:flex;align-items:center;padding-left:10px}
.f-signup{left:341px;top:91px;width:59px;height:18px;background:var(--blue);font-size:7px;font-weight:700;display:flex;align-items:center;justify-content:center}
.f-brand{left:562px;top:42px;display:flex;align-items:center;gap:7px;font-size:19px;font-weight:600}
.f-brand .brand-dot{background:var(--white)}
.f-rule{left:82px;top:158px;width:577px;height:1px;background:rgba(255,255,255,.25)}
.follow{left:82px;top:192px;font-size:7px;font-weight:700}
.social{top:187px;width:18px;height:18px;border-radius:50%;background:var(--blue)}
.copy{right:82px;top:192px;font-size:6px}
</style>
</head>
<body>

<header class="site-header">
  <div class="abs brand"><span class="brand-dot"></span>DialMetric</div>
  <div class="abs call">
    <span class="call-icon"><svg width="9" height="9" viewBox="0 0 24 24"><path fill="#fff" d="M6.6 10.8a15 15 0 0 0 6.6 6.6l2.2-2.2c.3-.3.7-.4 1-.2 1.1.4 2.3.6 3.6.6.6 0 1 .4 1 1V20c0 .6-.4 1-1 1A17 17 0 0 1 3 4c0-.6.4-1 1-1h3.5c.6 0 1 .4 1 1 0 1.3.2 2.5.6 3.6.1.3 0 .7-.2 1z"/></svg></span>
    <div><div class="call-label">CALL US NOW</div><div class="call-number">555.014.2270</div></div>
  </div>
  <div class="abs search"><svg width="6" height="6" viewBox="0 0 10 10"><circle cx="4" cy="4" r="3" fill="none" stroke="#333" stroke-width="1.4"/><path d="M6.3 6.3 9 9" stroke="#333" stroke-width="1.4"/></svg>SEARCH</div>
  <nav>
    <span class="abs nav" style="left:391px">WHO WE ARE</span>
    <span class="abs nav" style="left:458px">SERVICES</span>
    <span class="abs nav" style="left:514px">BLOG</span>
    <span class="abs nav is-active" style="left:557px">CONTACT</span>
    <span class="abs login"><svg width="6" height="7" viewBox="0 0 10 12"><rect x="1" y="5" width="8" height="7" fill="#fff"/><path d="M3 5V3a2 2 0 0 1 4 0v2" fill="none" stroke="#fff" stroke-width="1.5"/></svg>LOGIN</span>
  </nav>
</header>

<section class="abs hero">
</section>
<div class="abs hero-art" role="img" aria-label="Illustration of a call center agent with headset at a computer and a smiling customer on the phone, with chat bubbles and a 24/7 badge"></div>
<p class="abs hero-kicker">WE ARE A CALL CENTER</p>
<h1 class="abs hero-title">QUALITY ASSURANCE</h1>
<p class="abs hero-sub">AGENCY</p>

<h2 class="abs section-title">CONTACT US</h2>
<div class="abs title-rule"></div>

<div class="abs map" role="img" aria-label="Street map showing the office location"></div>

<h3 class="abs addr-head">ADDRESS</h3>
<p class="abs addr-line" style="top:521px">4410 Alder Crest Ave</p>
<p class="abs addr-line" style="top:538px">Linden, CA 91402</p>
<div class="abs addr-rule" style="top:566px"></div>
<p class="abs addr-mail">HELLO@DIALMETRIC.COM</p>
<div class="abs addr-rule" style="top:598px"></div>
<p class="abs addr-phone">555.014.2270</p>

<form class="abs form">
  <div class="field" style="left:26px;top:23px;width:163px;height:26px">NAME</div>
  <div class="field" style="left:202px;top:23px;width:163px;height:26px">E MAIL</div>
  <div class="field" style="left:376px;top:23px;width:163px;height:26px">SUBJECT</div>
  <div class="field" style="left:26px;top:64px;width:513px;height:80px">MESSAGE</div>
  <div class="submit">SUBMIT</div>
</form>

<footer class="abs footer">
  <h4 class="abs f-head" style="left:82px">MENU</h4>
  <div class="abs f-list" style="left:82px">Home<br>Who We Are<br>Services<br>Blog<br>Login</div>
  <h4 class="abs f-head" style="left:190px">CONTACT US</h4>
  <div class="abs f-list" style="left:190px">4410 Alder Crest Ave<br>Linden, CA 91402<br><br>hello@dialmetric.com<br><br>555.014.2270</div>
  <h4 class="abs f-head" style="left:340px">NEWSLETTER</h4>
  <div class="abs f-input">E MAIL ID</div>
  <div class="abs f-signup">SIGNUP</div>
  <div class="abs f-brand"><span class="brand-dot"></span>DialMetric</div>
  <div class="abs f-rule"></div>
  <p class="abs follow">FOLLOW US</p>
  <span class="abs social" style="left:137px;background:#1d4f95" aria-label="Social profile"></span>
  <span class="abs social" style="left:159px" aria-label="Social profile"></span>
  <span class="abs social" style="left:182px;background:#2f6aa8" aria-label="Social profile"></span>
  <span class="abs social" style="left:206px;background:#f26a3d" aria-label="Social profile"></span>
  <span class="abs social" style="left:231px;background:#1f7ac0" aria-label="Social profile"></span>
  <p class="abs copy">© 2017 DIALMETRIC. ALL RIGHTS RESERVED.</p>
</footer>

</body>
</html>
```